Mobile Fitness snd Therapy Business Card Design

I need a business card designed for my mobile fitness and therapy business.

Please view the images that I have uploaded. I like the simplicity of the design that I have attached. I adapted it with my information

Target Market(s)

Those seeking personal training, injury rehabilitation or massage therapy.

Industry/Entity Type

Business

Contact Information for Business Card

Derek Fulham - MSc, CAT(C), RMT, CSCS, Pn2
e-mail: derek@vantrelo.com
website: www.vantrelo.com
instagram: @derek_fulham

Font styles to use
Sans Serif

Colors
3176b5
0355a3

Requirements
Must have
• "Contact us to receive a FREE assessment"
• Services offered:
• Personal Training
• Golf Fitness
• Injury Rehab
• Massage Therapy
• Yoga
Nice to have
• Consistent colours with brand
• - Dark Blue: #232837
• - Blue: #5096f0
• Consistent look/feel with the website: www.vantrelo.com

```html
<!DOCTYPE html>
<html lang="en">
<head>
<meta charset="utf-8">
<title>Vantrelo Business Card</title>
<link href="https://fonts.googleapis.com/css2?family=Montserrat:wght@600;700&family=Open+Sans:wght@400&display=swap" rel="stylesheet">
<style>
  :root {
    --navy: #232837;
    --blue: #3176b5;
    --blue-light: #5096f0;
    --ink: #1b1e27;
    --paper: #ffffff;
    --backdrop: #e7e8eb;
  }
  * { margin: 0; padding: 0; box-sizing: border-box; }
  html, body { width: 1200px; height: 1000px; overflow: hidden; }
  body {
    position: relative;
    background: var(--backdrop);
    font-family: "Open Sans", Arial, sans-serif;
    color: var(--ink);
  }
  .card {
    position: absolute;
    left: 266px;
    width: 666px;
    height: 397px;
  }
  .card-front { top: 75px; background: var(--navy); }
  .card-back { top: 533px; background: var(--paper); }

  .brand-name {
    position: absolute;
    left: 0; right: 0; top: 222px;
    text-align: center;
    font-family: "Montserrat", Arial, sans-serif;
    font-weight: 600;
    font-size: 60px;
    letter-spacing: 6px;
    color: var(--paper);
    line-height: 1;
  }
  .brand-tagline {
    position: absolute;
    left: 0; right: 0; top: 294px;
    text-align: center;
    font-family: "Montserrat", Arial, sans-serif;
    font-weight: 700;
    font-size: 18px;
    letter-spacing: 2.6px;
    color: var(--paper);
  }

  .side-tab {
    position: absolute;
    top: 120px;
    width: 14px;
    height: 156px;
    background: var(--navy);
  }
  .side-tab-left { left: 0; }
  .side-tab-right { right: 0; }

  .contact { position: absolute; left: 72px; top: 118px; }
  .contact-name {
    font-family: "Montserrat", Arial, sans-serif;
    font-weight: 700;
    font-size: 21px;
    color: var(--ink);
    line-height: 28px;
  }
  .contact-credentials {
    font-size: 15px;
    color: var(--blue);
    line-height: 26px;
  }
  .contact-list { list-style: none; margin-top: 28px; }
  .contact-list li {
    display: flex;
    align-items: center;
    font-size: 17px;
    line-height: 26.5px;
  }
  .contact-list svg { width: 16px; height: 16px; margin-right: 7px; fill: var(--ink); }

  .divider {
    position: absolute;
    left: 332px; top: 122px;
    width: 2px; height: 154px;
    background: var(--navy);
  }

  .services { position: absolute; left: 388px; top: 114px; list-style: none; }
  .services li {
    display: flex;
    align-items: center;
    font-size: 18px;
    line-height: 23.6px;
  }
  .services li::before {
    content: "";
    width: 8px; height: 8px;
    margin-right: 11px;
    background: var(--blue-light);
  }

  .booking {
    position: absolute;
    left: 0; right: 0; top: 317px;
    text-align: center;
    font-size: 18px;
    line-height: 26px;
  }
  .booking a { color: var(--blue); text-decoration: none; }
</style>
</head>
<body>
  <section class="card card-front">
    <div class="brand-name">VANTRELO</div>
    <div class="brand-tagline">NUTRITION - FITNESS - HEALTH</div>
  </section>

  <section class="card card-back">
    <div class="side-tab side-tab-left"></div>
    <div class="side-tab side-tab-right"></div>

    <div class="contact">
      <div class="contact-name">DEREK FULHAM</div>
      <div class="contact-credentials">MSc, CAT(C), RMT, CSCS, Pn2</div>
      <ul class="contact-list">
        <li>
          <svg viewBox="0 0 16 16" aria-hidden="true"><path d="M1 6c0-2 3-3.5 7-3.5S15 4 15 6v1.2h-3.4V5.6H4.4v1.6H1zM4 8h8l2 5H2z"/></svg>
          250-555-0148
        </li>
        <li>
          <svg viewBox="0 0 16 16" aria-hidden="true"><path d="M1 3h14v10H1zm1.5 1.5v.4L8 8.6l5.5-3.7v-.4zm0 2.1v4.9h11V6.6L8 10.3z"/></svg>
          derek@vantrelo.com
        </li>
        <li>
          <svg viewBox="0 0 16 16" aria-hidden="true"><path d="M1.5 1.5h13v13h-13zm1.6 1.6v9.8h9.8V3.1z"/></svg>
          @vantrelo_kelowna
        </li>
      </ul>
    </div>

    <div class="divider"></div>

    <ul class="services">
      <li>Personal Training</li>
      <li>Group Training</li>
      <li>Nutrition Coaching</li>
      <li>Golf Fitness</li>
      <li>Injury Rehab</li>
      <li>Massage Therapy</li>
      <li>Yoga</li>
    </ul>

    <p class="booking">
      Services offered in-home or on location<br>
      Book a FREE assessment at <a href="#">www.vantrelo.com</a>
    </p>
  </section>
</body>
</html>
```